Thriller/Romance novel book cover design - Copper Tidewake

I need a book cover for a novel (print + ebook). Genre = thriller / romance. Title = Copper Tidewake. Author = Dorian Kell.
Story is set in Caribbean. 45-year-old Ex-OVK agent is hunted by corrupt politicians, OVK and cartel. He is a life-long fisherman and seaman who joined the Army after college and became a war hero, followed by 10 years as operative for the OVK. Betrayal from Washington saw him accused of killing his mentor/friend/OVK Director and he is now a fugitive. He has been hiding for 7 years on Grand Cayman, and lives a secluded, private life as a fisherman on his modern sportfisherman-style boat ('50 Velmora Convertible for reference). Boat name = Copper Tidewake (as in the playing card) represents fate to him and his high school sweetheart to whom he was engaged before a tragic event separated them. His main goal, beyond survival, is to reunite with his long, lost love, but he can't risk putting her in danger until he settles the case and those searching for him. The boat name (Copper Tidewake) only has relevance to him and his soulmate, who is not even aware that he is still alive.

Target Market(s)

thriller and romantic thriller readers

Requirements
Must have
• author name should be small on bottom of cover - not at top. Design is wide open for creative ideas. If a boat is used in artwork, it must be a modern sportfisherman style boat (google will define this
Nice to have
• I like intrigue and mystery. Don't try to explain or show too much. Prefer sunsets (orange, red, purple, yellow) to blue sky, blue water to give it a darker tone
Should not have
• do not want images of people on the cover like many romance novels do.

```html
<!DOCTYPE html>
<html lang="en">
<head>
<meta charset="utf-8">
<title>Copper Tidewake — Dorian Kell</title>
<link rel="stylesheet" href="https://fonts.googleapis.com/css2?family=Bodoni+Moda:wght@400;500&display=swap">
<style>
  :root {
    --page: #ffffff;
    --ink: #111010;
    --parchment-light: #dcc39e;
    --parchment: #c9aa80;
    --parchment-dark: #a98458;
    --sky-top: #b08c66;
    --dusk: #5c3b55;
    --dusk-deep: #3c2640;
    --ember: #d9252b;
    --flame: #f0701e;
    --gold: #f6b52c;
    --sea-glow: #b8361f;
    --sea-deep: #3a1210;
    --night: #120807;
    --author: #ffffff;
  }
  * { margin: 0; padding: 0; box-sizing: border-box; }
  html, body {
    width: 1200px; height: 1200px; overflow: hidden;
    background: var(--page);
  }
  .canvas {
    position: relative; width: 1200px; height: 1200px;
    background: var(--page);
  }
  .cover {
    position: absolute; left: 240px; top: 60px;
    width: 720px; height: 1128px; overflow: hidden;
  }
  .cover-art {
    position: absolute; inset: 0;
    background:
      radial-gradient(ellipse 420px 90px at 48% 705px, rgba(246,181,44,0.85), rgba(240,112,30,0) 70%),
      linear-gradient(180deg,
        var(--sky-top) 0px,
        var(--parchment-dark) 380px,
        var(--dusk) 500px,
        var(--dusk-deep) 560px,
        var(--ember) 620px,
        var(--flame) 700px,
        var(--gold) 770px,
        var(--flame) 790px,
        var(--sea-glow) 800px,
        var(--sea-deep) 930px,
        var(--night) 1128px);
  }
  .playing-card {
    position: absolute; left: 128px; top: 19px;
    width: 516px; height: 640px;
    border-radius: 26px;
    background:
      radial-gradient(ellipse at 40% 30%, var(--parchment-light), var(--parchment) 60%, var(--parchment-dark));
    box-shadow: inset 0 0 0 2px rgba(90,60,30,0.25), -4px 4px 10px rgba(60,35,15,0.35);
    -webkit-mask-image: linear-gradient(180deg, #000 0%, #000 62%, rgba(0,0,0,0.4) 82%, transparent 100%);
    mask-image: linear-gradient(180deg, #000 0%, #000 62%, rgba(0,0,0,0.4) 82%, transparent 100%);
  }
  .card-rank {
    position: absolute; left: 27px; top: 52px;
    font-family: "Bodoni Moda", serif; font-weight: 500;
    font-size: 80px; line-height: 1; color: var(--ink);
  }
  .card-pip-small { position: absolute; left: 24px; top: 144px; width: 50px; height: 54px; }
  .card-pip-large { position: absolute; left: 190px; top: 83px; width: 130px; height: 128px; }
  .title {
    position: absolute; left: 0; right: 0; top: 262px;
    text-align: center; color: var(--ink);
    font-family: "Bodoni Moda", serif; font-weight: 400;
  }
  .title-line-1 { display: block; font-size: 112px; line-height: 1; letter-spacing: 1px; }
  .title-line-2 { display: block; font-size: 132px; line-height: 1.05; letter-spacing: -1px; margin-top: 6px; }
  .author {
    position: absolute; left: 0; right: 0; top: 968px;
    text-align: center; color: var(--author);
    font-family: "Bodoni Moda", serif; font-weight: 400;
    font-size: 50px; letter-spacing: 5px;
  }
</style>
</head>
<body>
  <main class="canvas">
    <section class="cover">
      <div class="cover-art" role="img" aria-label="Photograph of a white modern sportfisherman boat with a tall tuna tower on a calm sea under a fiery orange, red and purple sunset"></div>

      <div class="playing-card" aria-hidden="true">
        <span class="card-rank">3</span>
        <svg class="card-pip-small" viewBox="0 0 100 108">
          <g fill="#111010">
            <circle cx="50" cy="26" r="24"/>
            <circle cx="24" cy="60" r="24"/>
            <circle cx="76" cy="60" r="24"/>
            <path d="M44 56 L56 56 L62 104 L38 104 Z"/>
          </g>
        </svg>
        <svg class="card-pip-large" viewBox="0 0 100 108">
          <g fill="#151211">
            <circle cx="50" cy="25" r="23"/>
            <circle cx="25" cy="58" r="23"/>
            <circle cx="75" cy="58" r="23"/>
            <path d="M45 50 L55 50 L64 106 L36 106 Z"/>
          </g>
        </svg>
      </div>

      <h1 class="title">
        <span class="title-line-1">Copper</span>
        <span class="title-line-2">Tidewake</span>
      </h1>

      <p class="author">Dorian Kell</p>
    </section>
  </main>
</body>
</html>
```